Soho based IT support firm flyer.

We need a flyer to boost our business. We're a tech support firm based in Soho, London and provide helpdesk and call out support to SMEs in and around London.
They'll be two flyers with the same design. One is location specific and has the copy:
-
1 Month Free IT Support!
Based in Soho, we provide expert tech support for both desktops and laptops.
We have monthly as well as pay-as-you-go plans to fit your business.
Call us now and we'll show you how we can save you up to 50% on your IT spend.
-None location based is-
1 Month Free IT Support!
We provide expert, professional tech support for both desktops and laptops.
• Dedicated full time helpdesk
• Same day onsite visits
• Proactive support with monitoring
• 98% satisfaction score*
*taken from satisfaction survey sent out on closure of every case for Oct 2011 to Oct 2012
-
The location one needs to include a map with our location marked as postcode K7R 4TB.
I'm fine with royalty photos being used within a reasonable price. Please use Pixmarrow.
Our site shows our brand best. Please keep as close to this as possible.
http://quillnet-hub.example
Thanks for looking.

```html
<!DOCTYPE html>
<html lang="en">
<head>
<meta charset="utf-8">
<title>QuillNet IT Support Flyer</title>
<link href="https://fonts.googleapis.com/css2?family=Arimo:wght@700&family=Roboto+Condensed:wght@400;700&display=swap" rel="stylesheet">
<style>
  :root {
    --lime: #a8cd3a;
    --lime-light: #c2dd5a;
    --orange: #f7941d;
    --orange-deep: #ee7d12;
    --charcoal: #4b4b4d;
    --ink: #3d3d3f;
    --white: #ffffff;
  }
  * { box-sizing: border-box; margin: 0; padding: 0; }
  html, body { width: 849px; height: 1200px; overflow: hidden; background: var(--white); }
  .flyer {
    position: relative;
    width: 849px;
    height: 1200px;
    overflow: hidden;
    background: linear-gradient(180deg, var(--lime-light) 0%, var(--lime) 100%);
    font-family: "Roboto Condensed", "Arial Narrow", sans-serif;
  }
  .headline {
    position: absolute;
    top: 28px; left: 0; right: 0;
    text-align: center;
    font-family: "Arimo", Arial, sans-serif;
    font-weight: 700;
    font-size: 52px;
    line-height: 1.1;
    color: var(--white);
    letter-spacing: -0.5px;
  }
  .hero-photo {
    position: absolute;
    top: 176px; left: 0;
    width: 849px; height: 440px;
    background: radial-gradient(ellipse at 55% 40%, #8c949c 0%, #5a6068 35%, #2e3236 75%, #1f2225 100%);
  }
  .free-badge {
    position: absolute;
    left: 688px; top: 410px;
    width: 182px; height: 182px;
    border-radius: 50%;
    background: var(--orange);
    border: 5px solid var(--white);
    transform: rotate(-14deg);
    color: var(--white);
    text-align: center;
    padding-top: 30px;
    padding-right: 18px;
  }
  .free-badge .free-word {
    display: block;
    font-family: "Arimo", Arial, sans-serif;
    font-weight: 700;
    font-size: 46px;
    line-height: 1;
  }
  .free-badge .free-offer {
    display: block;
    font-weight: 700;
    font-size: 23px;
    line-height: 1.08;
    margin-top: 6px;
  }
  .brand-tab {
    position: absolute;
    left: 0; top: 548px;
    width: 386px; height: 112px;
    background: var(--white);
    border-radius: 0 18px 18px 0;
    display: flex;
    align-items: center;
    padding-left: 40px;
    gap: 14px;
  }
  .brand-tab .brand-dot {
    width: 26px; height: 26px;
    border-radius: 50%;
    background: var(--lime);
  }
  .brand-tab .brand-name {
    font-family: "Arimo", Arial, sans-serif;
    font-weight: 700;
    font-size: 58px;
    color: var(--lime);
    letter-spacing: -1px;
  }
  .info-panel {
    position: absolute;
    left: 0; top: 672px;
    width: 849px; height: 528px;
    background: var(--charcoal);
  }
  .selling-points {
    position: absolute;
    left: 36px; top: 726px;
    width: 420px;
    list-style: none;
    color: var(--white);
    font-weight: 700;
    font-size: 29px;
    line-height: 1.07;
  }
  .selling-points li {
    position: relative;
    padding-left: 42px;
    margin-bottom: 20px;
  }
  .selling-points li::before {
    content: "";
    position: absolute;
    left: 0; top: 5px;
    width: 18px; height: 18px;
    border: 4px solid var(--white);
    border-radius: 50%;
  }
  .location-panel {
    position: absolute;
    left: 492px; top: 662px;
    width: 357px; height: 538px;
    background: linear-gradient(180deg, var(--orange) 0%, var(--orange-deep) 100%);
  }
  .map {
    position: absolute;
    left: 24px; top: 38px;
    width: 314px; height: 288px;
    border: 6px solid var(--white);
    background: linear-gradient(135deg, #ecebe4 0%, #dcdcd2 100%);
  }
  .map-pin {
    position: absolute;
    left: 116px; top: 90px;
  }
  .address {
    position: absolute;
    left: 30px; top: 350px;
    width: 310px;
    list-style: none;
    color: var(--white);
    font-size: 25px;
    line-height: 1.15;
  }
  .address li {
    position: relative;
    padding-left: 28px;
    margin-bottom: 10px;
  }
  .address li::before {
    content: "";
    position: absolute;
    left: 2px; top: 9px;
    width: 11px; height: 11px;
    background: var(--white);
  }
  .phone-bar {
    position: absolute;
    left: 0; top: 1114px;
    width: 492px; height: 86px;
    background: var(--lime);
    display: flex;
    align-items: center;
    padding-left: 22px;
    gap: 14px;
  }
  .phone-bar .phone-number {
    font-weight: 700;
    font-size: 56px;
    color: var(--ink);
    letter-spacing: 0.5px;
  }
</style>
</head>
<body>
<main class="flyer">
  <h1 class="headline">A one stop shop for all of<br>your business' IT needs.</h1>

  <div class="hero-photo" role="img" aria-label="Photo of a businessman in a suit touching a glowing digital interface"></div>

  <div class="free-badge">
    <span class="free-word">FREE</span>
    <span class="free-offer">One Month<br>IT Support!</span>
  </div>

  <div class="brand-tab">
    <span class="brand-dot"></span>
    <span class="brand-name">QuillNet</span>
  </div>

  <section class="info-panel"></section>

  <ul class="selling-points">
    <li>Based in Soho, we provide<br>expert tech support for both<br>desktops and laptops.</li>
    <li>We have monthly as well as<br>pay-as-you-go plans to fit<br>your business.</li>
    <li>Call us now and we'll show<br>you how we can save you up<br>to 50% on your IT spend.</li>
  </ul>

  <aside class="location-panel">
    <div class="map" role="img" aria-label="Street map of Soho with the office location marked">
      <svg class="map-pin" width="40" height="54" viewBox="0 0 40 54">
        <path d="M20 2C10 2 3 9.5 3 19c0 12 17 33 17 33s17-21 17-33C37 9.5 30 2 20 2z" fill="#e8452c"/>
        <circle cx="20" cy="19" r="6" fill="#ffffff"/>
      </svg>
    </div>
    <ul class="address">
      <li>12-14 Alder House,<br>Marlow Street,<br>London K7R 4TB</li>
      <li>info@quillnet-hub.example</li>
      <li>www.quillnet-hub.example</li>
    </ul>
  </aside>

  <div class="phone-bar">
    <svg width="46" height="46" viewBox="0 0 24 24" aria-hidden="true">
      <path fill="#ffffff" d="M6.6 10.8c1.4 2.8 3.8 5.1 6.6 6.6l2.2-2.2c.3-.3.7-.4 1-.2 1.1.4 2.3.6 3.6.6.6 0 1 .4 1 1V20c0 .6-.4 1-1 1C10.6 21 3 13.4 3 4c0-.6.4-1 1-1h3.5c.6 0 1 .4 1 1 0 1.3.2 2.5.6 3.6.1.3 0 .7-.2 1L6.6 10.8z"/>
    </svg>
    <span class="phone-number">0203 555 0142</span>
  </div>
</main>
</body>
</html>
```